The Sunlit Path To Quiet Harbors Book Cover

Book cover for a new book titled "The Sunlit Path To Quiet Harbors" which will show how retirees can pay NO tax in their retirement. Would like you to use your creative inspiration to come up with a design.

Please make QUIET HARBORS the emphasis of the title.

can you show money being rescued, or freed, from taxes.

I'm trying convey the message that retirees can FREE themselves from the burden of taxes in retirement by reading this book and following the instructions. Think about a person swimming with a weight on his back, sinking him. Suddenly the weight is removed. The feeling and imagery of the load being light now

Doing QUIET HARBORS can alleviate many of unnecessary taxes which will weight retirees down. But, unfortunately, many advisors in my industry do not educate their clients on this stuff.

Not a fan of dark backgrounds, generally speaking. Lighter is good.

Remember folks, go to brindlemart. Type in Roth IRA books. what will jump out over the stuff that's already there? Thanks!

Target Market(s)

recent, or soon to be, retirees, people in their 50s and 60s, typically couples

Industry/Entity Type

Financial

Font styles to use
Serif

Colors

Designer to choose colors to be used in the design.

Requirements
Must have
• Be optimistic, sunny, happy. How you do that? I don't know, that's why I'm hiring you. This book is designed for the lay person, (average Joe and Jane)
• Put my picture on the lower back.
• My name at bottom of the cover
Nice to have
• Be nice to have the cover POP on Brindlemart because I'm competing with so many other books and thumbnails
• Maybe a kite with a dollar bill that is breaking from a ball and chain? Just an idea.
Should not have
• No guys in suits. Happy couples sitting on the beach or sailing. That stuff is in every piece of financial planning literature.
• NOT TECHNICAL. NO PIGGY BANKS Design please

```html
<!DOCTYPE html>
<html lang="en">
<head>
<meta charset="utf-8">
<title>The Sunlit Path To Quiet Harbors — Book Cover</title>
<link rel="stylesheet" href="https://fonts.googleapis.com/css2?family=Montserrat:wght@400;500;600;700&display=swap">
<style>
  :root {
    --ink-teal: #135a74;
    --sky-top: #f4f9fc;
    --sky-mid: #dcedf6;
    --sky-low: #a9d3e6;
    --sea-deep: #2f8fb3;
    --sea-shore: #7cc4d6;
    --sand-light: #e4d8c3;
    --sand-dark: #c7b596;
    --band: rgba(240, 246, 249, 0.92);
  }
  * { margin: 0; padding: 0; box-sizing: border-box; }
  html, body {
    width: 841px;
    height: 1200px;
    overflow: hidden;
    background: #ffffff;
  }
  .cover {
    position: relative;
    width: 841px;
    height: 1200px;
    overflow: hidden;
    font-family: "Montserrat", sans-serif;
    color: var(--ink-teal);
  }
  .beach-scene {
    position: absolute;
    inset: 0;
    background: linear-gradient(
      to bottom,
      var(--sky-top) 0%,
      var(--sky-mid) 35%,
      var(--sky-low) 62%,
      var(--sea-deep) 64.5%,
      var(--sea-shore) 72%,
      var(--sand-light) 76%,
      var(--sand-dark) 100%
    );
  }
  .title-block {
    position: absolute;
    top: 138px;
    left: 0;
    width: 100%;
    text-align: center;
  }
  .title-kicker {
    font-weight: 400;
    font-size: 34px;
    letter-spacing: 0.5px;
    margin-left: -60px;
  }
  .title-main {
    font-weight: 600;
    font-size: 190px;
    line-height: 0.9;
    letter-spacing: 4px;
    margin-top: 14px;
  }
  .title-sub {
    font-weight: 600;
    font-size: 106px;
    line-height: 1;
    letter-spacing: 8px;
    margin-top: 8px;
  }
  .author-band {
    position: absolute;
    left: 0;
    top: 1110px;
    width: 100%;
    height: 66px;
    background: var(--band);
    display: flex;
    align-items: center;
    justify-content: center;
  }
  .author-name {
    font-weight: 500;
    font-size: 34px;
    letter-spacing: 6px;
  }
</style>
</head>
<body>
  <main class="cover">
    <div class="beach-scene" role="img" aria-label="Photograph of two blue wooden beach chairs on sand facing a calm turquoise sea under a pale sky"></div>

    <header class="title-block">
      <p class="title-kicker">The Sunlit Path To</p>
      <h1 class="title-main">QUIET</h1>
      <p class="title-sub">HARBORS</p>
    </header>

    <footer class="author-band">
      <p class="author-name">WES HALLORAN</p>
    </footer>
  </main>
</body>
</html>
```